Website Re-design for Kids Playhouse Business

Need current website which looks very outdated to be re-designed to look modern and contemporary, reduce clutter significantly and make it look elegant and simple.
Current website: http://www.tumblenest.com.au/
A website which the business owner likes, use as reference/inspiration: http://vexa.com.au/
Looking for light green palette, natural colours. "WHAT'S ON" page/link no longer required.
Industry/Entity Type
Business
Number of Pages Required
5+ page
Look and feel
Each slider illustrates characteristics of the customer's brand and the style your logo design should communicate.

```html
<!DOCTYPE html>
<html lang="en">
<head>
<meta charset="utf-8">
<title>Tumble Nest Playhouse &amp; Cafe</title>
<link rel="stylesheet" href="https://fonts.googleapis.com/css2?family=Poppins:ital,wght@0,400;0,500;0,600;0,700;1,500&display=swap">
<style>
:root{
  --green:#7fd05e;
  --green-deep:#6cc24a;
  --green-light:#93e36f;
  --white:#ffffff;
  --red:#e8202a;
  --ink:#333a2e;
  --grey-bg:#f4f4f2;
  --field:#ffffff;
  --field-line:#cfd6c9;
}
*{margin:0;padding:0;box-sizing:border-box}
html,body{width:1200px;height:4225px;overflow:hidden}
body{position:relative;font-family:'Poppins',sans-serif;background:var(--green);color:var(--white)}
.abs{position:absolute}
.center-text{text-align:center;left:0;width:1200px}

/* hero */
.hero-photo{left:0;top:0;width:1200px;height:760px;background:linear-gradient(135deg,#d9d4cc 0%,#c9b8a2 35%,#e6e1da 60%,#b7a690 100%)}
.slider-prev{left:34px;top:338px;width:34px;height:34px;border-radius:50%;border:2px solid rgba(255,255,255,.8);display:flex;align-items:center;justify-content:center}
.brand{left:170px;top:72px;display:flex;align-items:center;gap:12px}
.brand-dot{width:26px;height:26px;border-radius:50%;background:var(--green)}
.brand-name{font-weight:600;font-size:32px;line-height:1;color:var(--ink)}
.top-btn{top:64px;height:40px;border-radius:20px;font-size:14px;font-weight:500;display:flex;align-items:center;justify-content:center;gap:8px;color:var(--white)}
.btn-eclub{left:544px;width:174px;background:var(--red)}
.btn-call{left:727px;width:186px;background:var(--green)}
.btn-menu{left:930px;width:107px;background:var(--green)}
.main-nav{left:834px;top:124px;width:366px;height:513px;background:var(--green);padding-top:26px}
.main-nav a{display:block;text-align:center;color:var(--white);text-decoration:none;font-size:22px;line-height:53.5px}

/* sections */
.section-title{font-weight:600;font-size:36px;line-height:46px}
.lead{font-weight:600;font-size:18px;line-height:26px}
.body-copy{font-size:11px;line-height:19px}
.outline-btn{height:48px;border:2px solid var(--white);border-radius:24px;font-size:14px;font-weight:500;display:flex;align-items:center;justify-content:center;color:var(--white)}
.rule{left:0;width:1200px;top:1105px;height:1px;background:rgba(255,255,255,.35)}

.feature-photo{border-radius:50%;border:16px solid var(--green-deep);box-shadow:0 0 0 4px var(--green-light) inset,0 28px 24px -14px rgba(0,0,0,.18)}
.feature-block{width:400px}
.feature-title{font-weight:600;font-size:21px;line-height:28px}
.feature-copy{width:394px;font-size:11px;line-height:18px;margin-top:10px}
.feature-copy + .outline-btn{margin-top:20px}

.testimonial{font-weight:500;font-style:italic;font-size:17px;line-height:37px}
.author{font-weight:600;font-size:21px}
.dots span{display:inline-block;width:11px;height:11px;border-radius:50%;background:var(--green-deep);margin:0 2px}
.dots span.on{background:var(--white)}

.col-photo{border-radius:50%;border:10px solid var(--green-deep)}
.col-title{font-weight:600;font-size:30px;line-height:38px;text-align:center;width:300px}
.col-copy{font-size:11px;line-height:20px;text-align:center;width:290px}

.contact-title{font-weight:600;font-size:36px;line-height:44px;color:var(--green-deep)}
.contact-sub{font-size:14px;color:var(--ink)}
.field{background:var(--field);border:1px solid var(--field-line);border-radius:22px;height:40px;font-size:12px;color:var(--ink);padding:0 22px;display:flex;align-items:center}
.field.area{border-radius:20px;height:107px;align-items:flex-start;padding-top:14px}
.captcha{left:332px;top:3865px;width:255px;height:60px;background:var(--field);border:1px solid var(--field-line);border-radius:14px;color:var(--ink);font-size:9px;padding:8px 14px}
.send-btn{left:597px;top:3877px;width:144px;height:40px;border-radius:20px;background:var(--green);color:var(--white);font-size:12px;font-weight:600;display:flex;align-items:center;justify-content:center}

.footer-line{font-size:13px;font-weight:500}
.footer-small{font-size:11px;font-weight:500}
.social{top:4044px;width:30px;height:30px;border-radius:50%;background:rgba(255,255,255,.25);border:1px solid rgba(255,255,255,.6)}
</style>
</head>
<body>

<!-- Hero -->
<div class="abs hero-photo" role="img" aria-label="Photo of two toddlers playing with wooden toys in a playroom"></div>
<div class="abs slider-prev"><svg width="12" height="14" viewBox="0 0 12 14"><path d="M9 1 L3 7 L9 13" fill="none" stroke="#fff" stroke-width="2"/></svg></div>

<div class="abs brand"><span class="brand-dot"></span><span class="brand-name">Tumble Nest</span></div>

<div class="abs top-btn btn-eclub">Join Our E-club</div>
<div class="abs top-btn btn-call">Call: 02 9000 1234</div>
<div class="abs top-btn btn-menu"><svg width="14" height="12" viewBox="0 0 14 12"><rect y="0" width="14" height="2" fill="#fff"/><rect y="5" width="14" height="2" fill="#fff"/><rect y="10" width="14" height="2" fill="#fff"/></svg>Menu</div>

<nav class="abs main-nav">
  <a>Home</a><a>Hours &amp; Prices</a><a>Party Packages</a><a>Party Rooms</a><a>Vacation Care</a><a>School Holiday Program</a><a>Specials &amp; Promotions</a><a>Gallery</a>
</nav>

<svg class="abs" style="left:0;top:640px" width="1200" height="140" viewBox="0 0 1200 140">
  <path fill="#7fd05e" d="M0 70 Q60 30 130 60 Q200 20 280 60 Q340 40 400 60 Q440 0 520 40 Q600 -10 680 40 Q760 10 820 60 Q880 30 950 60 Q1020 20 1090 55 Q1150 35 1200 60 L1200 140 L0 140 Z"/>
</svg>

<!-- Welcome -->
<div class="abs center-text section-title" style="top:766px">Welcome to Tumble Nest</div>
<div class="abs center-text lead" style="top:822px">Sydney's newest and best party &amp; play centre!</div>
<p class="abs body-copy" style="left:260px;top:857px;width:680px;text-align:center">Tumble Nest is an indoor kids play centre and cafe that offers both kids and adults a chance to enjoy their time together. We pride ourselves in offering the best indoor play centre for your kids to engage in fun and learning activities in a specially created environment that is not only warm and safe but also enhances and stimulates creativity and curiosity in a child. Our centre offers variety in kids party venues like our themed party rooms which are hand painted. Our party rooms are uniquely designed and were built by local artists.</p>
<div class="abs outline-btn" style="left:518px;top:1013px;width:164px">Read More</div>
<div class="abs rule"></div>

<!-- Features -->
<div class="abs center-text section-title" style="top:1140px">Our Features</div>

<div class="abs feature-photo" style="left:234px;top:1234px;width:259px;height:259px;background:radial-gradient(circle,#f0c7d6,#c9a0d6 60%,#8fb6e0)" role="img" aria-label="Photo of a child at a decorated birthday party"></div>
<div class="abs feature-block" style="left:544px;top:1234px">
  <div class="feature-title">Perfect venue for<br>birthdays and private parties</div>
  <p class="feature-copy">Celebrate birthdays and private events in bright, safe rooms with friendly hosts, tasty party food and plenty of play time for every child. We handle setup and cleanup so parents can relax and enjoy the day.</p>
  <div class="outline-btn" style="width:164px">View Parties</div>
</div>

<div class="abs feature-block" style="left:234px;top:1531px">
  <div class="feature-title">4 kids loving<br>party rooms themes</div>
  <p class="feature-copy">Choose from four hand painted party rooms, each with its own story world. Kids step into castles, jungles, oceans and fairy gardens that spark their imagination from the moment they walk in.</p>
  <div class="outline-btn" style="width:164px">View Party rooms</div>
</div>
<div class="abs feature-photo" style="left:700px;top:1533px;width:259px;height:259px;background:radial-gradient(circle,#e9d9b2,#c98a5a 55%,#7fae5e)" role="img" aria-label="Photo of a hand painted fairytale themed party room"></div>

<div class="abs feature-photo" style="left:234px;top:1826px;width:259px;height:259px;background:radial-gradient(circle,#f2c39a,#c77c5a 55%,#6b5a8c)" role="img" aria-label="Photo of children with a costumed character at a holiday program"></div>
<div class="abs feature-block" style="left:544px;top:1826px">
  <div class="feature-title">We host school<br>holiday programs</div>
  <p class="feature-copy">Our school holiday program keeps children busy with crafts, games, shows and guided play. Book a single day or the whole week and let our caring staff look after the fun.</p>
  <div class="outline-btn" style="width:164px">View Programs</div>
</div>

<div class="abs feature-block" style="left:234px;top:2127px">
  <div class="feature-title">Exclusive specials<br>&amp; promotions</div>
  <p class="feature-copy">Watch for seasonal deals on entry, party packages and cafe treats. Join our e-club to hear about new offers first and save on your next family visit to the centre.</p>
  <div class="outline-btn" style="width:164px">View More</div>
</div>
<div class="abs feature-photo" style="left:688px;top:2122px;width:259px;height:259px;background:radial-gradient(circle,#7fd3f0,#2f8fc9 55%,#1f5c8f)" role="img" aria-label="Photo of a child playing in a colourful ball pit"></div>

<!-- Testimonial band -->
<svg class="abs" style="left:0;top:2400px" width="1200" height="1060" viewBox="0 0 1200 1060">
  <path fill="#93e36f" d="M0 110 Q80 60 170 95 Q250 40 340 80 Q420 50 500 70 Q540 0 600 0 Q660 0 700 70 Q780 40 860 80 Q950 40 1030 90 Q1120 55 1200 90 L1200 1060 L0 1060 Z"/>
</svg>
<div class="abs" style="left:580px;top:2494px;width:40px;height:40px;border-radius:50%;border:2px solid #fff;display:flex;align-items:center;justify-content:center"><svg width="16" height="12" viewBox="0 0 16 12"><path d="M1 11 V6 Q1 1 6 1 M9 11 V6 Q9 1 14 1" fill="none" stroke="#fff" stroke-width="1.6"/></svg></div>
<p class="abs testimonial" style="top:2565px;left:278px;width:645px;text-align:center">Love this place, lots of variety for the kids especially in school holidays !! They'll be entertained for hours whilst you enjoy delicious food or a great coffee !! Highly recommend it !!</p>
<div class="abs center-text author" style="top:2688px">-Maria Delos</div>
<div class="abs center-text dots" style="top:2747px"><span class="on"></span><span></span><span></span><span></span></div>

<!-- Info columns -->
<div class="abs col-photo" style="left:163px;top:2826px;width:245px;height:245px;background:radial-gradient(circle,#e0a06a,#9c3f2a 60%,#4a2a22)" role="img" aria-label="Photo of kids gathered around a party table"></div>
<div class="abs col-title" style="left:135px;top:3074px">Visit Us</div>
<p class="abs col-copy" style="left:140px;top:3128px">Find us close to shops and public transport, with easy parking right outside the door and a cafe inside for parents.</p>
<div class="abs outline-btn" style="left:203px;top:3258px;width:164px">View Location</div>

<div class="abs col-photo" style="left:478px;top:2900px;width:245px;height:245px;background:radial-gradient(circle,#e8e4ea,#9bb0d6 55%,#3c4a6e)" role="img" aria-label="Photo of children with a costumed bunny mascot"></div>
<div class="abs col-title" style="left:450px;top:3150px">About Us</div>
<p class="abs col-copy" style="left:455px;top:3204px">We are a family run play centre built around safe, creative play and good coffee for the grown ups who come too.</p>
<div class="abs outline-btn" style="left:518px;top:3331px;width:164px">Read More</div>

<div class="abs col-photo" style="left:794px;top:2824px;width:245px;height:245px;background:radial-gradient(circle,#c9a0c8,#6a8f5a 55%,#3a6a8a)" role="img" aria-label="Photo of a painted mural wall in a party room"></div>
<div class="abs col-title" style="left:766px;top:3074px">News</div>
<p class="abs col-copy" style="left:771px;top:3128px">Read the latest on new rooms, upcoming events, holiday dates and special days happening at the centre very soon.</p>
<div class="abs outline-btn" style="left:834px;top:3258px;width:164px">Read More</div>

<!-- Contact -->
<svg class="abs" style="left:0;top:3430px" width="1200" height="620" viewBox="0 0 1200 620">
  <path fill="#f4f4f2" d="M0 110 Q90 60 190 100 Q280 50 370 90 Q430 40 480 60 Q530 0 600 0 Q680 0 720 60 Q790 30 850 85 Q930 40 1020 90 Q1110 55 1200 95 L1200 620 L0 620 Z"/>
</svg>
<div class="abs center-text contact-title" style="top:3522px">Contact Us</div>
<div class="abs center-text contact-sub" style="top:3570px">Our postal address and contact details</div>

<div class="abs field" style="left:332px;top:3631px;width:263px">Name*:</div>
<div class="abs field" style="left:605px;top:3631px;width:263px">Phone*:</div>
<div class="abs field" style="left:332px;top:3684px;width:263px">Email*:</div>
<div class="abs field" style="left:605px;top:3684px;width:263px">Postcode*:</div>
<div class="abs field area" style="left:332px;top:3741px;width:536px">Message*:</div>
<div class="abs captcha">
  <div style="display:flex;align-items:center;gap:10px;font-size:13px">
    <svg width="18" height="18" viewBox="0 0 18 18"><path d="M15 9 A6 6 0 1 1 9 3 L12 3" fill="none" stroke="#6c7566" stroke-width="2"/><path d="M10 0 L13 3 L10 6" fill="none" stroke="#6c7566" stroke-width="2"/></svg>
    <span>25 + 9 =</span><span style="display:inline-block;width:60px;height:18px;border:1px solid var(--field-line)"></span>
  </div>
  <div style="margin-top:8px">Enter the answer to avoid spam</div>
</div>
<div class="abs send-btn">SEND MESSAGE</div>

<!-- Footer -->
<svg class="abs" style="left:0;top:3960px" width="1200" height="265" viewBox="0 0 1200 265">
  <path fill="#7fd05e" d="M0 60 Q90 20 180 55 Q260 25 340 50 Q420 10 500 35 Q560 0 620 20 Q690 0 740 35 Q820 10 900 50 Q980 20 1060 55 Q1130 30 1200 50 L1200 265 L0 265 Z"/>
</svg>
<div class="abs social" style="left:565px"></div>
<div class="abs social" style="left:602px"></div>
<div class="abs center-text footer-line" style="top:4100px">Postal Address: 14 Harbour Lane Westmead 2145 NSW Australia.</div>
<div class="abs center-text footer-line" style="top:4134px">Ph: 02 9000 1234 &nbsp;&nbsp;|&nbsp;&nbsp; Fax: 02 9000 1299 &nbsp;&nbsp;|&nbsp;&nbsp; Email: hello@tumblenestplay.com.au</div>
<div class="abs center-text footer-small" style="top:4175px">© 2018 Tumble Nest. All Rights Reserved. &nbsp;&nbsp; Terms &amp; Conditions &nbsp;&nbsp; Privacy Policy</div>

</body>
</html>
```